Steady Hands, professional newsletter for GAPM

** updated based on results so far** We need a 2 page newsletter designed on both sides of an 8.6 x 11 sheet back and front. Page one needs our logo below, name steady hands in large letters tagline of official newsletter of the guild of acute practice medicine volume and issue number locations It needs to include five locations for 250-400 word articles each with a spot for a picture. Page 2 needs to include contact information including address, phone number, email, twitter and facebook info below. The design need to complement out log in color, be professional with clean lines and easy to follow. We are a non profit organization dedicated to providers of urgent care medicine.

Target Market(s)

Physicians, Nurse Practitioners, Physician Assistants

Requirements
Must have
• 2 pages, back and front 8.5x 11
• 5 article area 250-400 words, one image for each
• our logo
• Name: Steady Hands - page one large visible print
• Contact inf:
• Guild of Acute Practice Medicine
• 912 Larkmoor Ave. Suite 418E
• Naperville, IL 60563
• 1 855-314-7093
• Info@gaopm.org
• @GuildAPM
Nice to have
• ease of entering info
• professional clean lines

```html
<!DOCTYPE html>
<html lang="en">
<head>
<meta charset="utf-8">
<title>Steady Hands – Locations &amp; Contact</title>
<link rel="stylesheet" href="https://fonts.googleapis.com/css2?family=Open+Sans:wght@400;600&amp;family=Source+Sans+3:wght@700&amp;display=swap">
<style>
  :root {
    --orange: #f7941d;
    --ink: #5b5b5b;
    --panel: #4a4846;
    --white: #ffffff;
  }
  * { box-sizing: border-box; margin: 0; padding: 0; }
  html, body { width: 1200px; height: 776px; overflow: hidden; background: var(--white); }
  .spread { position: relative; width: 1200px; height: 776px; overflow: hidden; font-family: "Open Sans", sans-serif; }

  .locations-page {
    position: absolute; left: 0; top: 0; width: 669px; height: 776px;
    background: linear-gradient(90deg, #f4f4f3 0%, #f7f6f4 40%, #eef3f5 60%, #f7f7f6 100%);
  }
  .locations-page::after {
    content: ""; position: absolute; inset: 0; background: rgba(255,255,255,0.72);
  }
  .locations-page__photo { position: absolute; inset: 0; }

  .location { position: absolute; left: 37px; width: 590px; height: 150px; z-index: 1; }
  .location__frame { position: absolute; left: 0; top: 0; width: 142px; height: 149px; background: var(--orange); }
  .location__photo {
    position: absolute; left: 10px; top: 10px; width: 139px; height: 130px;
    background: linear-gradient(135deg, #d9d2c0 0%, #b9b6ac 50%, #cfc3b4 100%);
  }
  .location__title {
    position: absolute; left: 179px; top: -8px;
    font-family: "Source Sans 3", sans-serif; font-weight: 700; font-size: 23px;
    color: var(--orange); letter-spacing: 0.1px;
  }
  .location__text {
    position: absolute; left: 179px; top: 30px; width: 378px;
    font-size: 14.2px; line-height: 21.6px; color: var(--ink);
  }
  .divider { position: absolute; left: 39px; width: 577px; height: 2px; background: var(--orange); z-index: 1; }

  .contact-page {
    position: absolute; left: 669px; top: 0; width: 531px; height: 776px;
    background: linear-gradient(160deg, #f1f0ee 0%, #e6e4e1 55%, #dcdad6 100%);
  }
  .contact-page__photo { position: absolute; inset: 0; }
  .contact-card {
    position: absolute; left: 26px; top: 319px; width: 479px; height: 422px;
    background: var(--panel); opacity: 0.97;
    border-top: 13px solid var(--orange); color: var(--white);
  }
  .contact-row { position: absolute; left: 0; width: 100%; }
  .contact-row__icon { position: absolute; left: 38px; }
  .contact-row__text { position: absolute; left: 93px; width: 358px; font-size: 14.2px; line-height: 24px; }
  .contact-row__phone { font-size: 31px; font-weight: 600; line-height: 36px; }
  .contact-row__web { font-size: 18.5px; line-height: 26px; }
</style>
</head>
<body>
<div class="spread">

  <section class="locations-page">
    <div class="locations-page__photo" role="img" aria-label="Faded background photo of a hospital corridor with visitors"></div>

    <article class="location" style="top:44px">
      <div class="location__frame"></div>
      <div class="location__photo" role="img" aria-label="Photo of three medical students practising on a training mannequin"></div>
      <h2 class="location__title">LOCATION 01</h2>
      <p class="location__text">Lorem ipsum dolor sit amet, consectetuer adipiscing elit. Aenean commodo ligula eget dolor. Aenean massa. Cum sociis natoque penatibus et magnis dis parturient montes, nascetur ridiculus mus. Donec quam felis, ultricies nec,</p>
    </article>
    <div class="divider" style="top:211px"></div>

    <article class="location" style="top:234px">
      <div class="location__frame"></div>
      <div class="location__photo" role="img" aria-label="Photo of three medical students practising on a training mannequin"></div>
      <h2 class="location__title">LOCATION 02</h2>
      <p class="location__text">Lorem ipsum dolor sit amet, consectetuer adipiscing elit. Aenean commodo ligula eget dolor. Aenean massa. Cum sociis natoque penatibus et magnis dis parturient montes, nascetur ridiculus mus. Donec quam felis, ultricies nec,</p>
    </article>
    <div class="divider" style="top:401px"></div>

    <article class="location" style="top:421px">
      <div class="location__frame"></div>
      <div class="location__photo" role="img" aria-label="Photo of three medical students practising on a training mannequin"></div>
      <h2 class="location__title">LOCATION 03</h2>
      <p class="location__text">Lorem ipsum dolor sit amet, consectetuer adipiscing elit. Aenean commodo ligula eget dolor. Aenean massa. Cum sociis natoque penatibus et magnis dis parturient montes, nascetur ridiculus mus. Donec quam felis, ultricies nec,</p>
    </article>
    <div class="divider" style="top:584px; width:575px"></div>

    <article class="location" style="top:604px">
      <div class="location__frame"></div>
      <div class="location__photo" role="img" aria-label="Photo of three medical students practising on a training mannequin"></div>
      <h2 class="location__title">LOCATION 04</h2>
      <p class="location__text">Lorem ipsum dolor sit amet, consectetuer adipiscing elit. Aenean commodo ligula eget dolor. Aenean massa. Cum sociis natoque penatibus et magnis dis parturient montes, nascetur ridiculus mus. Donec quam felis, ultricies nec,</p>
    </article>
  </section>

  <section class="contact-page">
    <div class="contact-page__photo" role="img" aria-label="Photo of a blue measuring tape wrapped around a dark pill bottle with yellow capsules"></div>

    <div class="contact-card">
      <div class="contact-row" style="top:33px">
        <svg class="contact-row__icon" style="top:2px" width="30" height="26" viewBox="0 0 30 26" aria-hidden="true">
          <path d="M2 11 L28 2 L20 24 L14 15 Z" fill="var(--white)"/>
          <path d="M14 15 L28 2" stroke="var(--panel)" stroke-width="1.6"/>
        </svg>
        <p class="contact-row__text">Guild of Acute Practice Medicine<br>912 Larkmoor Ave. Suite 418E, Naperville, IL 60563</p>
      </div>

      <div class="contact-row" style="top:131px">
        <svg class="contact-row__icon" style="top:6px" width="28" height="20" viewBox="0 0 28 20" aria-hidden="true">
          <rect x="1" y="1" width="26" height="18" fill="none" stroke="var(--white)" stroke-width="1.6"/>
          <path d="M1 1 L14 12 L27 1 M1 19 L11 10 M27 19 L17 10" fill="none" stroke="var(--white)" stroke-width="1.6"/>
        </svg>
        <p class="contact-row__text">Steady Hands is the official newsletter of the Guild of Acute Practice Medicine. Send your stories, questions and article ideas to Info@gaopm.org</p>
      </div>

      <div class="contact-row" style="top:262px">
        <svg class="contact-row__icon" style="top:6px" width="26" height="26" viewBox="0 0 24 24" aria-hidden="true">
          <path fill="var(--white)" d="M6.6 10.8c1.4 2.8 3.8 5.1 6.6 6.6l2.2-2.2c.3-.3.7-.4 1-.2 1.1.4 2.3.6 3.6.6.6 0 1 .4 1 1V20c0 .6-.4 1-1 1C10.6 21 3 13.4 3 4c0-.6.4-1 1-1h3.5c.6 0 1 .4 1 1 0 1.3.2 2.5.6 3.6.1.3 0 .7-.2 1L6.6 10.8z"/>
        </svg>
        <p class="contact-row__text contact-row__phone">1 855-314-7093</p>
      </div>

      <div class="contact-row" style="top:318px">
        <svg class="contact-row__icon" style="top:-2px" width="34" height="34" viewBox="0 0 34 34" aria-hidden="true">
          <circle cx="17" cy="17" r="15.5" fill="none" stroke="var(--white)" stroke-width="2"/>
        </svg>
        <p class="contact-row__text contact-row__web">www.friendpage.net/GuildAPM</p>
      </div>

      <div class="contact-row" style="top:362px">
        <svg class="contact-row__icon" style="top:-2px" width="34" height="34" viewBox="0 0 34 34" aria-hidden="true">
          <circle cx="17" cy="17" r="15.5" fill="none" stroke="var(--white)" stroke-width="2"/>
        </svg>
        <p class="contact-row__text contact-row__web">@GuildAPM</p>
      </div>
    </div>
  </section>

</div>
</body>
</html>
```